Business Landing Page for SEO Company

Need the landing page of the website designed - I will provide the copy, will need to include details of my company and the services offered, about us, testimonials, faq, etc., and all these elements will need to be arranged graphically on the page.

I want something similar to this: https://torvanequill.com/

Not in terms of color or theme or anything, but we offer a similar service and want to display similar information.

Th services we provide are:

Premium Links
Monthly Links Subscription
Link Insertions

Need to advertise them on the front page. Additionally need a place for testimonials, company details, etc.,

We already have logo for the website. Please use the attached file to insert the logo within the overal design.

Target Market(s)

SEO marketers and agencies

Number of Pages Required

1 page

```html
<!DOCTYPE html>
<html lang="en">
<head>
<meta charset="utf-8">
<title>Rankveil – SEO Company</title>
<link href="https://fonts.googleapis.com/css2?family=Montserrat:wght@500;600;700;800&family=Open+Sans:wght@400;600;700&display=swap" rel="stylesheet">
<style>
:root{
  --blue:#1f6fd6;
  --navy:#0b2a66;
  --orange:#f26a1b;
  --ink:#1b1b1b;
  --muted:#6b6b6b;
  --white:#ffffff;
  --footer:#101010;
  --star:#f4a51c;
}
*{box-sizing:border-box;margin:0;padding:0}
html,body{width:1200px;height:4480px;overflow:hidden}
body{font-family:"Open Sans",Arial,sans-serif;color:var(--ink);background:var(--white);position:relative}
.section{position:absolute;left:0;width:1200px}
h2.section-title{font-family:"Montserrat",Arial,sans-serif;font-weight:800;font-size:38px;text-align:center;letter-spacing:1px}
h2.section-title::after{content:"";display:block;width:70px;height:4px;background:var(--blue);margin:12px auto 0}
.btn{display:inline-block;background:var(--orange);color:var(--white);font-family:"Montserrat",Arial,sans-serif;font-weight:700;font-size:15px;letter-spacing:.5px;padding:16px 30px;text-transform:uppercase;white-space:nowrap}
.body-text{font-size:14px;line-height:22px;color:var(--muted)}

/* hero */
.hero{top:0;height:600px;background:linear-gradient(90deg,#e7cfb4 0%,#efdcc6 45%,#d9b896 100%)}
.hero-photo{position:absolute;inset:0}
.nav{position:absolute;top:0;left:0;width:1200px;height:60px;display:flex;align-items:center;padding:0 100px}
.brand{font-family:"Montserrat",Arial,sans-serif;font-weight:800;font-size:32px;color:var(--white);letter-spacing:.5px}
.nav ul{list-style:none;display:flex;gap:38px;margin-left:auto;font-family:"Montserrat",Arial,sans-serif;font-size:14px;font-weight:600;color:#2c2c2c}
.nav li.active{color:var(--blue);border-bottom:2px solid var(--blue);padding-bottom:4px}
.hero-copy{position:absolute;left:108px;top:210px}
.hero-copy h1{font-family:"Montserrat",Arial,sans-serif;font-weight:800;font-size:60px;color:var(--blue);letter-spacing:1px}
.hero-copy p{font-family:"Montserrat",Arial,sans-serif;font-weight:700;font-size:22px;color:var(--white);margin:10px 0 40px}
.hero-seo{position:absolute;left:470px;top:80px;width:320px;height:280px;border-radius:12px;background:radial-gradient(circle,#f5e9d8,#e9d3b8)}
.hero-person{position:absolute;left:820px;top:40px;width:260px;height:500px;border-radius:40px;background:linear-gradient(180deg,#d9b19a,#2fb8b0 70%,#1f8f88)}
.dots{position:absolute;left:568px;top:555px;display:flex;gap:8px}
.dots span{width:8px;height:8px;border-radius:50%;background:rgba(255,255,255,.7)}
.dots span:first-child{background:var(--white)}

/* offer */
.offer{top:600px;height:590px}
.offer .section-title{margin-top:90px}
.offer-cards{display:flex;justify-content:center;gap:22px;margin-top:60px}
.offer-card{width:314px;height:350px;background:var(--white);box-shadow:0 2px 14px rgba(0,0,0,.12);text-align:center;padding:30px 24px}
.offer-card svg{width:70px;height:70px}
.offer-card h3{font-family:"Montserrat",Arial,sans-serif;font-size:16px;font-weight:700;margin:22px 0 14px;white-space:nowrap}
.offer-card .btn{margin-top:22px;padding:13px 26px;font-size:13px}

/* about */
.about{top:1190px;height:520px;background:var(--blue)}
.about-photo{position:absolute;left:10px;top:30px;width:570px;height:420px;background:linear-gradient(135deg,#4f6c8a,#c9d3de 55%,#8aa3bb)}
.about-copy{position:absolute;left:650px;top:90px;width:420px;color:var(--white)}
.about-copy h2{font-family:"Montserrat",Arial,sans-serif;font-weight:800;font-size:38px}
.about-copy h2::after{content:"";display:block;width:70px;height:4px;background:var(--white);margin:10px 0 24px}
.about-copy p{font-size:14px;line-height:22px;color:#eaf1fc}
.about-copy .btn{margin-top:40px}

/* testimonials */
.testimonials{top:1710px;height:870px}
.testimonials .section-title{margin-top:76px}
.testimonial-grid{display:grid;grid-template-columns:repeat(3,296px);gap:20px;justify-content:center;margin-top:50px}
.testimonial{height:260px;background:var(--white);box-shadow:0 2px 12px rgba(0,0,0,.12);padding:24px 22px;position:relative}
.testimonial .who{display:flex;align-items:center;gap:12px;font-weight:700;font-size:15px;margin-bottom:16px}
.avatar{width:40px;height:40px;border-radius:50%;background:#9aa4ad}
.testimonial p{font-size:13px;line-height:20px;color:#555}
.stars{color:var(--star);font-size:20px;letter-spacing:2px;margin-top:8px}
.quote{position:absolute;right:20px;bottom:6px;font-family:Georgia,serif;font-size:90px;line-height:90px;color:var(--blue);font-weight:700}

/* cta */
.cta{top:2580px;height:400px;background:linear-gradient(90deg,#3b3a38 0%,#6d6458 45%,#b49a7e 70%,#8e7a66 100%)}
.cta-copy{position:absolute;left:110px;top:100px;color:var(--white)}
.cta-copy h2{font-family:"Montserrat",Arial,sans-serif;font-weight:800;font-size:40px;line-height:48px;width:540px}
.cta-copy .btn{margin-top:28px;font-size:13px;padding:13px 26px}

/* news */
.news{top:2980px;height:630px}
.news .section-title{margin-top:76px}
.news-grid{display:flex;justify-content:center;gap:20px;margin-top:50px}
.news-card{width:300px}
.news-card .thumb{height:200px}
.news-card h3{font-family:"Montserrat",Arial,sans-serif;font-size:19px;font-weight:700;margin:22px 0 10px}
.news-card p{font-size:13px;line-height:20px;color:var(--muted)}
.news-card .more{font-family:"Montserrat",Arial,sans-serif;color:var(--orange);font-weight:700;font-size:13px;margin-top:16px;display:block}

/* faq */
.faq{top:3610px;height:400px;background:radial-gradient(circle at 70% 40%,#1e5fc9,#0b2f7a 70%)}
.faq-list{position:absolute;left:112px;top:60px;width:440px;color:var(--white)}
.faq-list h2{font-family:"Montserrat",Arial,sans-serif;font-weight:800;font-size:26px;margin-bottom:18px}
.faq-item{font-weight:700;font-size:15px;margin-top:14px;display:flex;justify-content:space-between}
.faq-item.open{margin-top:0}
.faq-list p{font-size:13px;line-height:19px;color:#dbe6fb;margin-top:8px}
.faq-form{position:absolute;left:640px;top:75px;width:420px}
.field{height:40px;border:1px solid rgba(255,255,255,.55);color:#e4ecfb;font-size:13px;padding:10px 14px;margin-bottom:12px}
.field-row{display:flex;gap:12px}.field-row .field{flex:1}
.field.message{height:92px}
.faq-form .btn{font-size:13px;padding:13px 22px}

/* footer */
.footer{top:4010px;height:470px;background:var(--footer);color:#cfcfcf}
.footer .brand{position:absolute;left:110px;top:76px;font-size:38px}
.footer-col{position:absolute;top:90px;font-size:13px;line-height:22px}
.footer-col h4{font-family:"Montserrat",Arial,sans-serif;color:var(--white);font-size:15px;font-weight:700;margin-bottom:16px;letter-spacing:.5px}
.footer-col svg{width:14px;height:14px;vertical-align:-2px;margin-right:8px}
.signup{display:flex;margin-top:16px}
.signup .input{width:220px;height:38px;background:var(--white);color:#888;font-size:12px;padding:10px}
.signup .go{width:40px;height:38px;background:var(--orange);display:flex;align-items:center;justify-content:center}
.socials{display:flex;gap:12px;margin-top:12px}
.socials span{width:16px;height:16px;background:#d9d9d9}
.footer-bar{position:absolute;left:0;bottom:0;width:1200px;height:70px;border-top:1px solid #2a2a2a;display:flex;align-items:center;padding:0 112px;font-size:12px}
.footer-bar ul{list-style:none;display:flex;gap:28px;margin-left:auto;color:var(--white)}
</style>
</head>
<body>

<header class="section hero">
  <div class="hero-photo" role="img" aria-label="Warm beige wall backdrop"></div>
  <div class="hero-seo" role="img" aria-label="SEO doodle illustration"></div>
  <div class="hero-person" role="img" aria-label="Woman with a laptop sitting in a teal armchair"></div>
  <nav class="nav">
    <div class="brand">Rankveil</div>
    <ul>
      <li class="active">HOME</li><li>SERVICES</li><li>ABOUT US</li><li>TESTIMONIALS</li><li>FAQ</li><li>CONTACT US</li>
    </ul>
  </nav>
  <div class="hero-copy">
    <h1>RANKVEIL</h1>
    <p>WE ARE AN SEO COMPANY</p>
    <span class="btn">Get Started</span>
  </div>
  <div class="dots"><span></span><span></span><span></span><span></span></div>
</header>

<section class="section offer">
  <h2 class="section-title">WHAT WE OFFER</h2>
  <div class="offer-cards">
    <article class="offer-card">
      <svg viewBox="0 0 70 70" fill="none" stroke="var(--blue)" stroke-width="2.5"><path d="M15 25 L25 14 H45 L55 25 L35 56 Z"/><path d="M15 25 H55 M25 14 L35 56 L45 14" stroke="var(--orange)"/></svg>
      <h3>Premium Links</h3>
      <p class="body-text">Lorem ipsum dolor sit amet, consectetur adipiscing elit, sed do eiusmod tempor incididunt ut labore et dolore magna aliqua.</p>
      <span class="btn">Learn More</span>
    </article>
    <article class="offer-card">
      <svg viewBox="0 0 70 70" fill="none" stroke="var(--blue)" stroke-width="2.5"><rect x="12" y="12" width="46" height="46"/><path d="M44 26 L26 44 M26 30 V44 H40" stroke="var(--orange)" stroke-width="3"/></svg>
      <h3>Link Insertions</h3>
      <p class="body-text">Lorem ipsum dolor sit amet, consectetur adipiscing elit, sed do eiusmod tempor incididunt ut labore et dolore magna aliqua.</p>
      <span class="btn">Learn More</span>
    </article>
    <article class="offer-card">
      <svg viewBox="0 0 70 70" fill="none" stroke="var(--blue)" stroke-width="2.5"><rect x="10" y="14" width="50" height="44" rx="4"/><path d="M10 26 H60 M22 8 V18 M48 8 V18"/><path d="M20 34 h6 M32 34 h6 M44 34 h6 M20 44 h6 M32 44 h6 M44 44 h6" stroke="var(--orange)" stroke-width="4"/></svg>
      <h3>Monthly Links Subscription</h3>
      <p class="body-text">Lorem ipsum dolor sit amet, consectetur adipiscing elit, sed do eiusmod tempor incididunt ut labore et dolore magna aliqua.</p>
      <span class="btn">Learn More</span>
    </article>
  </div>
</section>

<section class="section about">
  <div class="about-photo" role="img" aria-label="Hands typing on a laptop showing SEO analytics"></div>
  <div class="about-copy">
    <h2>ABOUT US</h2>
    <p>Lorem ipsum dolor sit amet, consectetur adipiscing elit, sed do eiusmod tempor incididunt ut labore et dolore magna aliqua. Quis ipsum suspendisse ultrices gravida. Risus commodo viverra maecenas accumsan lacus vel facilisis. Lorem ipsum dolor sit amet, consectetur adipiscing elit, sed do eiusmod tempor incididunt ut labore et dolore magna aliqua. Quis ipsum suspendisse ultrices gravida. Risus commodo viverra maecenas accumsan lacus vel facilisis.</p>
    <span class="btn">Learn More</span>
  </div>
</section>

<section class="section testimonials">
  <h2 class="section-title">TESTIMONIALS</h2>
  <div class="testimonial-grid">
    <article class="testimonial"><div class="who"><span class="avatar"></span>Delia Marsh</div><p>Our backlinks arrived on time and every site was relevant. Rankings climbed within weeks. Clear reporting and friendly support throughout.</p><div class="stars">★★★★★</div><span class="quote">”</span></article>
    <article class="testimonial"><div class="who"><span class="avatar"></span>John Smith</div><p>Lorem ipsum dolor sit amet, consectetur adipiscing elit, sed do eiusmod tempor incididunt ut labore et dolore magna aliqua. Quis ipsum.</p><div class="stars">★★★★★</div><span class="quote">”</span></article>
    <article class="testimonial"><div class="who"><span class="avatar"></span>John Smith</div><p>Lorem ipsum dolor sit amet, consectetur adipiscing elit, sed do eiusmod tempor incididunt ut labore et dolore magna aliqua. Quis ipsum.</p><div class="stars">★★★★★</div><span class="quote">”</span></article>
    <article class="testimonial"><div class="who"><span class="avatar"></span>Delia Marsh</div><p>Our backlinks arrived on time and every site was relevant. Rankings climbed within weeks. Clear reporting and friendly support throughout.</p><div class="stars">★★★★★</div><span class="quote">”</span></article>
    <article class="testimonial"><div class="who"><span class="avatar"></span>John Smith</div><p>Lorem ipsum dolor sit amet, consectetur adipiscing elit, sed do eiusmod tempor incididunt ut labore et dolore magna aliqua. Quis ipsum.</p><div class="stars">★★★★★</div><span class="quote">”</span></article>
    <article class="testimonial"><div class="who"><span class="avatar"></span>John Smith</div><p>Lorem ipsum dolor sit amet, consectetur adipiscing elit, sed do eiusmod tempor incididunt ut labore et dolore magna aliqua. Quis ipsum.</p><div class="stars">★★★★★</div><span class="quote">”</span></article>
  </div>
</section>

<section class="section cta" role="img" aria-label="Smiling businesswoman in a city street at dusk">
  <div class="cta-copy">
    <h2>GROW YOUR BUSINESS WITH RELIABLE SOUTH WEST COAST SEO.</h2>
    <span class="btn">Schedule a Free Consultation</span>
  </div>
</section>

<section class="section news">
  <h2 class="section-title">NEWS FEED</h2>
  <div class="news-grid">
    <article class="news-card"><div class="thumb" role="img" aria-label="Team meeting around a laptop" style="background:linear-gradient(135deg,#c9d6e3,#7f97ad)"></div><h3>Lorem ipsum dolor sit amet</h3><p>Lorem ipsum dolor sit amet, consectetur adipiscing elit, sed do eiusmod tempor incididunt ut labore et dolore magna aliqua.</p><span class="more">LEARN MORE →</span></article>
    <article class="news-card"><div class="thumb" role="img" aria-label="Magnifier over SEO search screen" style="background:linear-gradient(135deg,#e6ecf2,#9fb3c7)"></div><h3>Lorem ipsum dolor sit amet</h3><p>Lorem ipsum dolor sit amet, consectetur adipiscing elit, sed do eiusmod tempor incididunt ut labore et dolore magna aliqua.</p><span class="more">LEARN MORE →</span></article>
    <article class="news-card"><div class="thumb" role="img" aria-label="Chalkboard SEO diagram" style="background:linear-gradient(135deg,#2b2b2b,#4a4a4a)"></div><h3>Lorem ipsum dolor sit amet</h3><p>Lorem ipsum dolor sit amet, consectetur adipiscing elit, sed do eiusmod tempor incididunt ut labore et dolore magna aliqua.</p><span class="more">LEARN MORE →</span></article>
  </div>
</section>

<section class="section faq">
  <div class="faq-list">
    <h2>GOT QUESTIONS?</h2>
    <div class="faq-item open"><span>The standard Lorem Ipsum passage, used since?</span><span>−</span></div>
    <p>Lorem ipsum dolor sit amet, consectetur adipiscing elit, sed do eiusmod tempor incididunt ut labore et dolore magna aliqua. Quis ipsum suspendisse ultrices gravida.</p>
    <div class="faq-item"><span>The standard Lorem Ipsum passage, used since?</span><span>+</span></div>
    <div class="faq-item"><span>The standard Lorem Ipsum passage, used since?</span><span>+</span></div>
    <div class="faq-item"><span>The standard Lorem Ipsum passage, used since?</span><span>+</span></div>
    <div class="faq-item"><span>The standard Lorem Ipsum passage, used since?</span><span>+</span></div>
    <div class="faq-item"><span>The standard Lorem Ipsum passage, used since?</span><span>+</span></div>
  </div>
  <div class="faq-form">
    <div class="field">Name</div>
    <div class="field">Email</div>
    <div class="field-row"><div class="field">Country Code</div><div class="field">Phone</div></div>
    <div class="field message">Message</div>
    <span class="btn">Schedule a Free Consultation</span>
  </div>
</section>

<footer class="section footer">
  <div class="brand">Rankveil</div>
  <div class="footer-col" style="left:355px">
    <h4>CONTACT</h4>
    <div><svg viewBox="0 0 14 14"><path d="M7 1a4 4 0 0 0-4 4c0 3 4 8 4 8s4-5 4-8a4 4 0 0 0-4-4z" fill="var(--orange)"/></svg>123 Avenue name, City name</div>
    <div style="padding-left:22px">10700, United States</div>
    <div><svg viewBox="0 0 14 14"><path d="M3 1h3l1 3-2 1a7 7 0 0 0 4 4l1-2 3 1v3a1 1 0 0 1-1 1A12 12 0 0 1 2 2a1 1 0 0 1 1-1z" fill="var(--orange)"/></svg>888 888 8888</div>
    <div><svg viewBox="0 0 14 14"><rect x="1" y="3" width="12" height="8" fill="var(--orange)"/><path d="M1 3l6 5 6-5" stroke="#101010" fill="none"/></svg>info@rankveil.com</div>
  </div>
  <div class="footer-col" style="left:595px;width:280px">
    <h4>NEWSLETTER SIGNUP</h4>
    <div>Join our community and receive latest news &amp; updates about our company and our offer.</div>
    <div class="signup"><div class="input">Email</div><div class="go"><svg viewBox="0 0 14 14" style="margin:0"><path d="M2 7h9M8 4l3 3-3 3" stroke="#fff" stroke-width="2" fill="none"/></svg></div></div>
  </div>
  <div class="footer-col" style="left:905px;width:200px">
    <h4>FOLLOW US</h4>
    <div>Visit &amp; Follow Rankveil on our social media accounts</div>
    <div class="socials"><span></span><span></span><span></span><span></span></div>
  </div>
  <div class="footer-bar">
    <span>© 2020 Rankveil. All Rights Reserved.</span>
    <ul><li>Home</li><li>Our Services</li><li>Testimonials</li><li>Blog</li><li>About</li><li>Contact</li></ul>
  </div>
</footer>

</body>
</html>
```